Bed Company needs business card

Hello, we are a bed company that makes specialized magnets for beds. We are an alternative healing company. I need a modern and upscale business card. Please incorporate my logo for the card.

Accepted file formats are AI, EPS, and Press-Ready PDFS.

Please include all fonts or convert them to outlines regardless of file type.

If you are designing the card in Photoshop the file Must be 1200dpi.

I am open to anything for the business card.  I really like all of your designs and if you want to change the color of the logo, you can.  I will be making the final selection by Friday.  Thank You for all of your designs.  Feel Free to submit different color logos if you want.  

Reason: I will make a decision Final on Friday April 20th. 2012. Good Luck and Thank you all for the designs.

Target Market(s)

My target Market is people, who are looking for alternative healing.

Industry/Entity Type

Business

Requirements
Must have
• My logo must be incorporated. The front card must have

Name
Job Title

Address
Work
Cell
Fax
email
web

Just put in fake info for the card.

The back of the card. I want the logo on the back with color. I just want it to look modern and cool.

```html
<!DOCTYPE html>
<html lang="en">
<head>
<meta charset="utf-8">
<title>Fernleaf Rest — Business Card</title>
<link rel="stylesheet" href="https://fonts.googleapis.com/css2?family=Carlito:wght@400;700&display=swap">
<style>
  :root {
    --backdrop: #e9e9e6;
    --leaf: #55b848;
    --forest: #0e6233;
    --brand-green: #2f9a3d;
    --paper: #ffffff;
    --rule: #ffffff;
  }
  html, body {
    margin: 0;
    padding: 0;
    overflow: hidden;
  }
  .canvas {
    position: relative;
    width: 1200px;
    height: 900px;
    background: var(--backdrop);
    font-family: "Carlito", "Calibri", sans-serif;
    overflow: hidden;
  }
  .card {
    position: absolute;
    width: 620px;
    height: 354px;
    box-shadow: 0 6px 18px rgba(0,0,0,0.18);
    overflow: hidden;
  }
  /* Front */
  .card-front {
    left: 60px;
    top: 80px;
    background: var(--forest);
  }
  .panel {
    position: absolute;
    background: var(--leaf);
    box-sizing: border-box;
  }
  .panel-top-left {
    left: 0; top: 0;
    width: 260px; height: 70px;
    border-right: 4px solid var(--rule);
    border-bottom: 4px solid var(--rule);
  }
  .panel-top-right {
    left: 360px; top: 0;
    width: 260px; height: 70px;
    border-left: 4px solid var(--rule);
    border-bottom: 4px solid var(--rule);
  }
  .panel-bottom-left {
    left: 0; top: 152px;
    width: 260px; height: 202px;
    border-right: 4px solid var(--rule);
    border-top: 4px solid var(--rule);
  }
  .panel-bottom-right {
    left: 360px; top: 152px;
    width: 260px; height: 202px;
    border-left: 4px solid var(--rule);
    border-top: 4px solid var(--rule);
  }
  .identity {
    position: absolute;
    left: 0; right: 0;
    top: 86px;
    text-align: center;
    color: var(--paper);
  }
  .identity-name {
    margin: 0;
    font-size: 34px;
    font-weight: 400;
    line-height: 1;
  }
  .identity-title {
    margin: 2px 0 0;
    font-size: 18px;
    line-height: 1.1;
  }
  .contact {
    position: absolute;
    left: 34px;
    top: 210px;
    color: var(--paper);
    font-size: 15px;
    line-height: 19px;
  }
  .contact-row {
    display: grid;
    grid-template-columns: 42px 14px auto;
  }
  .contact-links {
    margin-top: 18px;
  }
  .contact-email { color: var(--paper); }
  .contact-web { color: var(--forest); }
  .event {
    position: absolute;
    left: 388px;
    top: 180px;
    color: var(--paper);
    font-size: 15px;
    line-height: 19px;
  }
  .event-company { margin: 0 0 22px; }
  .event-details { margin: 0; }
  /* Back */
  .card-back {
    left: 520px;
    top: 466px;
    background: var(--paper);
  }
  .brand {
    position: absolute;
    inset: 0;
    display: flex;
    align-items: center;
    justify-content: center;
    gap: 18px;
  }
  .brand-square {
    width: 58px;
    height: 58px;
    background: var(--forest);
  }
  .brand-name {
    font-size: 52px;
    font-weight: 700;
    color: var(--brand-green);
    line-height: 1;
  }
</style>
</head>
<body>
<main class="canvas">
  <section class="card card-front" aria-label="Business card front">
    <div class="panel panel-top-left"></div>
    <div class="panel panel-top-right"></div>
    <div class="panel panel-bottom-left"></div>
    <div class="panel panel-bottom-right"></div>

    <header class="identity">
      <h1 class="identity-name">Dorian Pell</h1>
      <p class="identity-title">director</p>
    </header>

    <div class="contact">
      <div class="contact-row"><span>tel</span><span>:</span><span>(999) 999 999</span></div>
      <div class="contact-row"><span>cell</span><span>:</span><span>(999) 999 000</span></div>
      <div class="contact-row"><span>fax</span><span>:</span><span>(999) 000 000</span></div>
      <div class="contact-links">
        <div class="contact-email">office@fernleafrest.com</div>
        <div class="contact-web">www.fernleaf-rest.com</div>
      </div>
    </div>

    <div class="event">
      <p class="event-company">Fernleaf Rest, Ltd</p>
      <p class="event-details">June 5-8, 2012,<br>Harbor Hall East,<br>Denver CO, Booth 2260</p>
    </div>
  </section>

  <section class="card card-back" aria-label="Business card back">
    <div class="brand">
      <span class="brand-square"></span>
      <span class="brand-name">Fernleaf Rest</span>
    </div>
  </section>
</main>
</body>
</html>
```